BRIGHTHOLD PROPERTY MANAGEMENT INC. WEBSITE

Please make the website more family-friendly.

I want a website to help me build my property management business by adding listing properties and creating an online application. Im open to any other ideas.
I want a WordPress designer to code it.

Here is my current website. www.brighthold.biz

IDEA: I like the website design https://www.pelicanclimateservices.com/

Thank you

Tom

Number of Pages Required

5+ page

```html
<!DOCTYPE html>
<html lang="en">
<head>
<meta charset="utf-8">
<title>Brighthold Property Management</title>
<link rel="stylesheet" href="https://fonts.googleapis.com/css2?family=Cinzel:wght@400;500&family=Roboto:wght@400;500;700&display=swap">
<style>
:root{
  --red:#a3141c;
  --red-dark:#7e0d13;
  --navy:#14233a;
  --ink:#1b1b1b;
  --text:#333;
  --muted:#666;
  --line:#9a9a9a;
  --white:#fff;
  --black:#0b0b0b;
}
*{box-sizing:border-box;margin:0;padding:0}
html,body{width:1200px;height:4444px;overflow:hidden}
body{position:relative;font-family:"Roboto",Arial,sans-serif;color:var(--text);background:var(--white)}
.abs{position:absolute}
.serif{font-family:"Cinzel",Georgia,serif}
.btn{position:absolute;display:flex;align-items:center;justify-content:center;font:500 15px "Roboto",Arial,sans-serif;text-transform:uppercase;clip-path:polygon(12% 0,100% 0,88% 100%,0 100%)}
.btn-red{background:var(--red);color:var(--white)}
.btn-white{background:var(--white);color:var(--ink)}
.accent{color:var(--red)}
.rule{position:absolute;height:3px;width:70px;background:var(--white)}

/* header */
.site-header{position:absolute;left:0;top:0;width:1200px;height:100px;background:var(--white)}
.brand{position:absolute;left:110px;top:30px;display:flex;align-items:center;gap:10px}
.brand-mark{width:26px;height:26px;background:var(--red)}
.brand-name{font:500 22px "Cinzel",Georgia,serif;color:var(--red);letter-spacing:1px}
.phone{position:absolute;left:735px;top:8px;display:flex;align-items:center;gap:10px;font:500 15px Roboto,sans-serif;color:var(--ink)}
.phone .dot{width:42px;height:42px;border-radius:50%;background:var(--red);display:flex;align-items:center;justify-content:center}
.nav{position:absolute;left:440px;top:66px;display:flex;gap:31px;font:500 13px Roboto,sans-serif;color:var(--ink);letter-spacing:.3px}

/* hero */
.hero{position:absolute;left:0;top:100px;width:1200px;height:642px;background:linear-gradient(100deg,rgba(20,30,40,.35) 0%,rgba(20,30,40,0) 50%),linear-gradient(180deg,#6f8aa3 0%,#8d9aa0 28%,#7d7a5a 52%,#4a5236 75%,#27301f 100%)}

/* about */
.house-frame{position:absolute}
.section-title{font:400 34px "Cinzel",Georgia,serif;color:var(--ink)}
.body-copy{font:400 14.5px/28px Roboto,sans-serif;color:var(--text);text-align:justify}
.body-copy p+p{margin-top:14px}

/* listings */
.listing-band{position:absolute;left:0;top:1418px;width:1200px;height:766px;background:linear-gradient(180deg,#16243b 0%,#1f2a3c 45%,#3a2218 80%,#2a1a14 100%);clip-path:polygon(0 44px,860px 0,1200px 30px,1200px 100%,0 100%)}
.card{position:absolute;top:1627px;width:314px;height:410px;background:var(--white)}
.card-photo{height:251px;background:linear-gradient(180deg,#e7e3dc 0%,#d3cdc3 60%,#8a6a4e 100%)}
.card h3{margin-top:18px;font:500 16px/26px Roboto,sans-serif;color:var(--ink);text-align:center;padding:0 40px}
.card .price{margin-top:8px;font:400 15px Roboto,sans-serif;color:var(--text);text-align:center}
.card .specs{display:flex;justify-content:center;align-items:center;gap:22px;margin-top:12px;font:400 14px Roboto,sans-serif;color:var(--ink)}
.card .specs span{display:flex;align-items:center;gap:6px}
.card .corner{position:absolute;right:-2px;bottom:-2px;width:26px;height:26px;border-radius:50%;background:var(--black)}

/* applicants */
.applicants{position:absolute;left:0;top:2877px;width:1200px;height:461px;background:linear-gradient(180deg,#b0222a,#8f141b)}
.feature{position:absolute;top:3070px;width:290px;text-align:center;color:var(--white)}
.feature h4{font:400 21px "Cinzel",Georgia,serif;margin-top:14px}
.feature p{font:400 14px/26px Roboto,sans-serif;margin-top:8px}
.feature a{display:inline-block;margin-top:6px;font:700 14px Roboto,sans-serif;color:var(--white);text-decoration:underline}
.arrow{position:absolute;top:3172px;width:36px;height:36px;border-radius:50%;display:flex;align-items:center;justify-content:center}

/* form */
.field-label{position:absolute;font:500 13.5px Roboto,sans-serif;color:var(--ink)}
.field{position:absolute;border:1px solid var(--line);background:var(--white);font:400 13px Roboto,sans-serif;color:var(--muted);display:flex;align-items:center;padding:0 8px;justify-content:space-between}

/* footer */
.site-footer{position:absolute;left:0;top:4050px;width:1200px;height:394px;background:var(--black);color:var(--white)}
.footer-brand{position:absolute;left:110px;top:170px;font:500 30px "Cinzel",Georgia,serif;letter-spacing:1px}
.footer-brand small{display:block;font-size:10px;letter-spacing:2px;margin-top:4px}
.footer-h{position:absolute;font:500 19px Roboto,sans-serif}
.quick-links{position:absolute;left:400px;top:112px;list-style:none;font:400 15px/31px Roboto,sans-serif}
.contact-item{position:absolute;left:607px;display:flex;gap:16px;font:400 15px/24px Roboto,sans-serif}
.contact-item b{font-weight:500}
.contact-icon{width:42px;height:42px;border-radius:50%;background:var(--red);flex:none;display:flex;align-items:center;justify-content:center;margin-top:6px}
.social{position:absolute;top:4148px;width:32px;height:32px;border-radius:50%;border:2px solid var(--white)}
.copyright{position:absolute;left:0;width:1200px;text-align:center;font:400 15px Roboto,sans-serif}
</style>
</head>
<body>

<header class="site-header">
  <div class="brand"><span class="brand-mark"></span><span class="brand-name">BRIGHTHOLD</span></div>
  <div class="phone">
    <span class="dot"><svg width="18" height="18" viewBox="0 0 24 24"><path fill="#fff" d="M6.6 10.8a15 15 0 006.6 6.6l2.2-2.2c.3-.3.7-.4 1-.2 1.1.4 2.3.6 3.6.6.6 0 1 .4 1 1V20c0 .6-.4 1-1 1A17 17 0 013 4c0-.6.4-1 1-1h3.5c.6 0 1 .4 1 1 0 1.3.2 2.5.6 3.6.1.3 0 .7-.2 1z"/></svg></span>
    +1(555) 010 2040
  </div>
  <div class="btn btn-red" style="left:945px;top:8px;width:145px;height:42px">Login Now</div>
  <nav class="nav"><span>LISTINGS</span><span>OWNERS</span><span>PROSPECT TENANTS</span><span>ABOUT</span><span>COMMUNITY</span><span>MORTGAGE INFO</span></nav>
</header>

<section class="hero" role="img" aria-label="Photo of a riverside city skyline with a stepped golden office building and trees"></section>
<div class="abs" style="left:110px;top:278px;font:400 26px Roboto,sans-serif;color:#fff;letter-spacing:1px">WELCOME TO</div>
<div class="abs serif" style="left:108px;top:318px;font-size:56px;color:#fff;letter-spacing:1px">BRIGHTHOLD</div>
<div class="abs serif" style="left:110px;top:386px;font-size:24px;color:#fff">PROPERTY MANAGEMENT</div>
<div class="btn btn-white" style="left:110px;top:428px;width:158px;height:42px">Get Started</div>

<!-- about -->
<svg class="house-frame" style="left:112px;top:845px" width="446" height="493" viewBox="0 0 446 493" role="img" aria-label="Photo of a house with a For Rent sign in the front yard">
  <defs><linearGradient id="aboutFill" x1="0" y1="0" x2="0" y2="1"><stop offset="0" stop-color="#9bb5cf"/><stop offset=".5" stop-color="#cfc9bd"/><stop offset="1" stop-color="#6d7f4a"/></linearGradient></defs>
  <polygon points="3,78 223,3 443,78 443,490 3,490" fill="url(#aboutFill)" stroke="#a3141c" stroke-width="6"/>
</svg>
<h2 class="abs section-title" style="left:648px;top:860px">ABOUT <span class="accent">US</span></h2>
<div class="abs body-copy" style="left:650px;top:954px;width:440px">
  <p>Our vision for Brighthold Property Management is to provide the best Property Management Services to the Lakeport and surrounding areas. I am focused on providing a more personalized service to you and your tenants. This means we are a one-stop-shop. You only deal with me, no middle guy, so no time is wasted.</p>
  <p>Brighthold Property Management is operated and owned by me Thomas Marlowe I have over 10 years of experience in property management combined with real estate appraising and understand the importance of 'return on investment.</p>
</div>
<div class="btn btn-red" style="left:650px;top:1268px;width:158px;height:44px">Read More</div>

<!-- listings -->
<div class="listing-band" role="img" aria-label="Night photo of a lit river bridge and waterfront"></div>
<h2 class="abs serif" style="left:0;top:1506px;width:1200px;text-align:center;font-size:34px;color:#fff">OUR LISITING</h2>
<div class="rule" style="left:565px;top:1560px"></div>

<article class="card" style="left:110px">
  <div class="card-photo" role="img" aria-label="Photo of an empty apartment room with wood floors"></div>
  <h3>Nice &amp; Clean 3 bd. x 1 bth. Apartment.</h3>
  <div class="price">$1,695.00</div>
  <div class="specs"><span><svg width="26" height="20" viewBox="0 0 26 20"><path d="M2 18V6h22v12M2 13h22M5 9h7" fill="none" stroke="#333" stroke-width="1.6"/></svg>2</span><span><svg width="22" height="20" viewBox="0 0 22 20"><path d="M3 10h16v3a5 5 0 01-5 5H8a5 5 0 01-5-5zM5 10V3h4" fill="none" stroke="#333" stroke-width="1.6"/></svg>1</span><span>693 Sq. Ft.</span></div>
  <span class="corner"></span>
</article>
<article class="card" style="left:443px">
  <div class="card-photo" role="img" aria-label="Photo of an empty unit with windows and a refrigerator"></div>
  <h3>Fantastic opportunity 2 Bdrm x 1 Bth ADU Unit!!</h3>
  <div class="price">$2,000.00</div>
  <div class="specs"><span><svg width="26" height="20" viewBox="0 0 26 20"><path d="M2 18V6h22v12M2 13h22M5 9h7" fill="none" stroke="#333" stroke-width="1.6"/></svg>2</span><span><svg width="22" height="20" viewBox="0 0 22 20"><path d="M3 10h16v3a5 5 0 01-5 5H8a5 5 0 01-5-5zM5 10V3h4" fill="none" stroke="#333" stroke-width="1.6"/></svg>1</span><span>693 Sq. Ft.</span></div>
  <span class="corner"></span>
</article>
<article class="card" style="left:776px">
  <div class="card-photo" role="img" aria-label="Photo of a bright empty room with tiled floor"></div>
  <h3>418 Willow Ave<br>#3</h3>
  <div class="price">$1,695.00</div>
  <div class="specs"><span><svg width="26" height="20" viewBox="0 0 26 20"><path d="M2 18V6h22v12M2 13h22M5 9h7" fill="none" stroke="#333" stroke-width="1.6"/></svg>2</span><span><svg width="22" height="20" viewBox="0 0 22 20"><path d="M3 10h16v3a5 5 0 01-5 5H8a5 5 0 01-5-5zM5 10V3h4" fill="none" stroke="#333" stroke-width="1.6"/></svg>1</span><span>693 Sq. Ft.</span></div>
  <span class="corner"></span>
</article>
<div class="btn btn-white" style="left:521px;top:2083px;width:158px;height:42px">View Details</div>

<!-- property manager -->
<h2 class="abs section-title" style="left:113px;top:2268px;line-height:46px">PROPERTY MANAGER <span class="accent">FOR<br>YOUR RENTAL</span></h2>
<div class="abs" style="left:115px;top:2370px;width:70px;height:3px;background:var(--red)"></div>
<div class="abs body-copy" style="left:113px;top:2406px;width:482px">
  <p>Vacancy periods are significantly reduced with an extensive pool of prospective renters as well as free advertising.Save on repairs. I have negotiated with maintenance contractors and receive discounts that are passed on to you.I perform extensive background checks on prospective renters to minimize your overall vacancy rate and potential non-payments of rent.</p>
  <p>No more calling maintenance specialists and waiting for them to show up. No more having to deal with the time-consuming rent collections, following up on third party issues associated with the property, and sometimes tenant complaints. I</p>
</div>
<div class="btn btn-red" style="left:113px;top:2727px;width:158px;height:44px">Read More</div>
<svg class="house-frame" style="left:645px;top:2285px" width="446" height="493" viewBox="0 0 446 493" role="img" aria-label="Photo of a hand holding a tablet beside a small model house on blueprints">
  <defs><linearGradient id="mgrFill" x1="0" y1="0" x2="1" y2="1"><stop offset="0" stop-color="#3b4550"/><stop offset=".55" stop-color="#c9c6c2"/><stop offset="1" stop-color="#f1f0ee"/></linearGradient></defs>
  <polygon points="3,78 223,3 443,78 443,490 3,490" fill="url(#mgrFill)" stroke="#a3141c" stroke-width="6"/>
</svg>

<!-- applicants -->
<section class="applicants" role="img" aria-label="Photo of a modern house with garage, tinted red"></section>
<h2 class="abs serif" style="left:0;top:2922px;width:1200px;text-align:center;font-size:34px;line-height:46px;color:#fff">RENTAL APPLICANTS AND<br>PROSPECTIVE TENANTS</h2>
<div class="rule" style="left:565px;top:3025px"></div>

<div class="arrow" style="left:44px;border:2px solid #fff"><svg width="14" height="14" viewBox="0 0 14 14"><path d="M9 2L4 7l5 5" fill="none" stroke="#fff" stroke-width="2"/></svg></div>
<div class="arrow" style="left:1120px;background:#fff"><svg width="14" height="14" viewBox="0 0 14 14"><path d="M5 2l5 5-5 5" fill="none" stroke="#a3141c" stroke-width="2"/></svg></div>

<div class="feature" style="left:101px">
  <svg width="48" height="48" viewBox="0 0 48 48"><path d="M18 8h12l-3 7h-6zM21 15c-8 4-12 12-12 18 0 7 6 10 15 10s15-3 15-10c0-6-4-14-12-18" fill="none" stroke="#fff" stroke-width="2"/><text x="24" y="35" font-size="13" fill="#fff" text-anchor="middle" font-family="Roboto">$</text></svg>
  <h4>INCOME</h4>
  <p>In order to rent a residential home from Brighthold Property Management Inc.,</p>
  <a>READ MORE</a>
</div>
<div class="feature" style="left:455px">
  <svg width="52" height="48" viewBox="0 0 52 48"><circle cx="18" cy="14" r="7" fill="none" stroke="#fff" stroke-width="2"/><path d="M5 40c0-9 6-14 13-14s13 5 13 14z" fill="none" stroke="#fff" stroke-width="2"/><circle cx="36" cy="18" r="6" fill="none" stroke="#fff" stroke-width="2"/><path d="M34 30h14v12H34z" fill="none" stroke="#fff" stroke-width="2"/></svg>
  <h4>REFERENCES:</h4>
  <p>We will want to contact your current and perhaps your former landlord for references.</p>
  <a>READ MORE</a>
</div>
<div class="feature" style="left:822px">
  <svg width="48" height="48" viewBox="0 0 48 48"><path d="M8 4h24v38H8z" fill="none" stroke="#fff" stroke-width="2"/><path d="M13 12h14M13 18h14M13 24h9" stroke="#fff" stroke-width="2"/><rect x="22" y="28" width="22" height="14" rx="2" fill="#fff"/></svg>
  <h4>CREDIT REPORTS</h4>
  <p>The credit report is one of several factors we use in choosing a tenant.</p>
  <a>READ MORE</a>
</div>

<!-- property information form -->
<h2 class="abs section-title" style="left:0;top:3428px;width:1200px;text-align:center">PROPERTY <span class="accent">INFORMATION</span></h2>

<label class="field-label" style="left:222px;top:3522px">Type of property</label>
<label class="field-label" style="left:488px;top:3522px">Number of bedrooms</label>
<label class="field-label" style="left:759px;top:3522px">Square Footage</label>
<div class="field" style="left:221px;top:3553px;width:234px;height:44px">Signal Family <svg width="14" height="10" viewBox="0 0 14 10"><path d="M2 2l5 5 5-5" fill="none" stroke="#333" stroke-width="1.6"/></svg></div>
<div class="field" style="left:488px;top:3553px;width:233px;height:44px"></div>
<div class="field" style="left:758px;top:3553px;width:234px;height:44px"></div>

<label class="field-label" style="left:222px;top:3626px">Number of bathrooms</label>
<label class="field-label" style="left:488px;top:3626px">Property Address</label>
<label class="field-label" style="left:759px;top:3626px">City, State , Postal Code</label>
<div class="field" style="left:221px;top:3658px;width:234px;height:44px"></div>
<div class="field" style="left:488px;top:3658px;width:233px;height:44px"></div>
<div class="field" style="left:758px;top:3658px;width:65px;height:44px"></div>
<div class="field" style="left:834px;top:3658px;width:85px;height:44px;color:#1b1b1b">Select <svg width="12" height="8" viewBox="0 0 12 8"><path d="M1 1l5 5 5-5" fill="none" stroke="#333" stroke-width="1.4"/></svg></div>
<div class="field" style="left:930px;top:3658px;width:64px;height:44px"></div>

<label class="field-label" style="left:222px;top:3720px">Additional features or upgrades</label>
<div class="field" style="left:221px;top:3748px;width:771px;height:122px"></div>
<div class="btn btn-red" style="left:521px;top:3910px;width:158px;height:42px">Submit</div>

<!-- footer -->
<footer class="site-footer">
  <div class="footer-brand">BRIGHTHOLD<small>PROPERTY MANAGEMENT &amp; SERVICES</small></div>
  <div class="footer-h" style="left:400px;top:70px">Quick Links</div>
  <ul class="quick-links"><li>Listings</li><li>Owners</li><li>Prospect Tenants</li><li>About</li><li>Community</li><li>Mortgage Info</li></ul>
  <div class="footer-h" style="left:607px;top:66px">Contact Us</div>
  <div class="contact-item" style="top:116px">
    <span class="contact-icon"><svg width="18" height="14" viewBox="0 0 18 14"><rect x="1" y="1" width="16" height="12" fill="#fff"/><path d="M1 1l8 6 8-6" fill="none" stroke="#a3141c" stroke-width="1.5"/></svg></span>
    <div><b>Email:</b><br>info@brighthold.biz</div>
  </div>
  <div class="contact-item" style="top:192px">
    <span class="contact-icon"><svg width="18" height="18" viewBox="0 0 24 24"><path fill="#fff" d="M6.6 10.8a15 15 0 006.6 6.6l2.2-2.2c.3-.3.7-.4 1-.2 1.1.4 2.3.6 3.6.6.6 0 1 .4 1 1V20c0 .6-.4 1-1 1A17 17 0 013 4c0-.6.4-1 1-1h3.5c.6 0 1 .4 1 1 0 1.3.2 2.5.6 3.6.1.3 0 .7-.2 1z"/></svg></span>
    <div><b>Phone No:</b><br>(555) 014-7788</div>
  </div>
  <div class="contact-item" style="top:266px">
    <span class="contact-icon"><svg width="16" height="20" viewBox="0 0 16 20"><path d="M8 0a8 8 0 00-8 8c0 6 8 12 8 12s8-6 8-12a8 8 0 00-8-8z" fill="#fff"/><circle cx="8" cy="8" r="3" fill="#a3141c"/></svg></span>
    <div><b>Location:</b><br>480 Harbor View Rd. #12<br>Lakeport , CA 95453</div>
  </div>
  <div class="footer-h" style="left:917px;top:66px">Follow Us</div>
  <div class="copyright" style="top:350px">Copyright © 2024 Brighthold. All Rights Reserved.</div>
</footer>
<span class="social" style="left:920px" aria-label="Social profile"></span>
<span class="social" style="left:963px" aria-label="Social profile"></span>
<span class="social" style="left:1005px" aria-label="Social profile"></span>
<span class="social" style="left:1047px" aria-label="Social profile"></span>

</body>
</html>
```